Business Card for beauty technology startup

Design Glimora Business Card for a Beauty, based on the website identity and colors (https://www.glimora-example.com).
Glimora is a beauty tech startup that gathers helpful product info for beauty lovers and consumers (such as availability on stores, price range and product reviews) for makeup products. The card design must be young, colorful but clean, and very modern.

Target Market(s)

woman, 15-35

Industry/Entity Type

Cosmetics

Contact Information for Business Card

Full Name, address, phone

Font styles to use
Other font styles liked:
• Advent Pro

Colors
e34297
86cfc6
ffffff
5c5c5c
e8e8e8
e667a6
b2b2b2

Requirements
Must have
• One full colored side with a creative design and another with card info
• Use Color palette: #95C5C5 and/or #D38AA5
• Use fonts: Advent Pro
• Use website identity: https://www.glimora-example.com
Nice to have
• If needed extra font: Roboto

```html
<!DOCTYPE html>
<html lang="en">
<head>
<meta charset="utf-8">
<title>Glimora Business Card</title>
<link rel="stylesheet" href="https://fonts.googleapis.com/css2?family=Advent+Pro:wght@300;400&family=Roboto:wght@400;500&display=swap">
<style>
  :root {
    --rose: #b87d92;
    --ink: #1b1c1e;
    --paper: #f4f4f3;
    --text: #4a4a4a;
    --white: #ffffff;
    --backdrop: #d9d9d9;
  }
  html, body {
    margin: 0;
    padding: 0;
    width: 1200px;
    height: 960px;
    overflow: hidden;
    background: var(--backdrop);
  }
  .canvas {
    position: relative;
    width: 1200px;
    height: 960px;
  }
  .card {
    position: absolute;
    width: 600px;
    height: 342px;
    border-radius: 22px;
    overflow: hidden;
  }
  .card-front { left: 314px; top: 113px; background: var(--paper); }
  .card-back  { left: 311px; top: 472px; background: var(--ink); }

  .name-band {
    position: absolute;
    left: 0;
    top: 50px;
    width: 274px;
    height: 134px;
    background: var(--rose);
  }
  .brand-circle {
    position: absolute;
    left: 208px;
    top: 50px;
    width: 130px;
    height: 130px;
    border-radius: 50%;
    background: var(--paper);
    border: 2px solid var(--rose);
    box-sizing: border-box;
  }
  .holder-name {
    position: absolute;
    left: 28px;
    top: 91px;
    margin: 0;
    font: 500 19px/1 "Roboto", sans-serif;
    color: var(--white);
  }
  .holder-role {
    position: absolute;
    left: 29px;
    top: 126px;
    margin: 0;
    font: 400 15px/1 "Roboto", sans-serif;
    color: var(--white);
  }
  .wordmark {
    font-family: "Advent Pro", sans-serif;
    font-weight: 300;
    color: var(--rose);
    margin: 0;
    line-height: 1;
  }
  .card-front .wordmark {
    position: absolute;
    left: 367px;
    top: 78px;
    font-size: 40px;
    letter-spacing: 3px;
  }
  .address {
    position: absolute;
    left: 369px;
    top: 160px;
    margin: 0;
    font: 400 14.5px/18px "Roboto", sans-serif;
    color: var(--text);
    font-style: normal;
  }
  .contacts {
    position: absolute;
    left: 370px;
    top: 205px;
    margin: 0;
    padding: 0;
    list-style: none;
    font: 400 14.5px/19px "Roboto", sans-serif;
    color: var(--text);
  }
  .contacts li { display: flex; align-items: center; gap: 8px; }
  .contacts svg { width: 14px; height: 14px; fill: var(--rose); flex: none; }

  .back-circle {
    position: absolute;
    left: 250px;
    top: 80px;
    width: 100px;
    height: 100px;
    border-radius: 50%;
    border: 2px solid var(--rose);
    box-sizing: border-box;
  }
  .card-back .wordmark {
    position: absolute;
    left: 0;
    width: 600px;
    top: 212px;
    text-align: center;
    font-size: 46px;
    letter-spacing: 4px;
  }
  .back-url {
    position: absolute;
    left: 0;
    width: 600px;
    top: 296px;
    margin: 0;
    text-align: center;
    font: 400 14px/1 "Roboto", sans-serif;
    letter-spacing: 4px;
    color: var(--white);
  }
</style>
</head>
<body>
<main class="canvas">
  <section class="card card-front" aria-label="Card front">
    <div class="name-band"></div>
    <div class="brand-circle"></div>
    <p class="holder-name">MARA QUINLAN</p>
    <p class="holder-role">CEO/FOUNDER</p>
    <h1 class="wordmark">GLIMORA</h1>
    <address class="address">2140 Linden Court<br>Juneau, Alaska 34511</address>
    <ul class="contacts">
      <li><svg viewBox="0 0 16 16"><path d="M3 1l3 3-1.5 2c1 2 3 4 5 5L11.5 9.5l3 3-2 2.5C7 14 2 9 1 3z"/></svg>555 214 0387</li>
      <li><svg viewBox="0 0 16 16"><path d="M4 0h8a1 1 0 011 1v14a1 1 0 01-1 1H4a1 1 0 01-1-1V1a1 1 0 011-1zm1 2v10h6V2zm3 11a1 1 0 100 2 1 1 0 000-2z"/></svg>555 731 4426</li>
      <li><svg viewBox="0 0 16 16"><path d="M4 1h8v4H4zM1 6h14v6h-3v3H4v-3H1zm4 5v3h6v-3z"/></svg>555 908 1152</li>
      <li><svg viewBox="0 0 16 16"><path d="M1 3h14v10H1zm1 1l6 5 6-5z"/></svg>info@glimora-example.com</li>
      <li><svg viewBox="0 0 16 16"><circle cx="8" cy="8" r="7"/></svg>www.glimora-example.com</li>
    </ul>
  </section>

  <section class="card card-back" aria-label="Card back">
    <div class="back-circle"></div>
    <h2 class="wordmark">GLIMORA</h2>
    <p class="back-url">www.glimora-example.com</p>
  </section>
</main>
</body>
</html>
```